Graphics for New Online Software

Looking at a designer to design a UI/UX Interface for an Online Events Platform (just JPEG) and some corresponding images for a website content (i.e. features etc)

Deliverables:
1x User Interface Design for the Platform (refer to attachment)
5-6x Feature Listing Images (refer to attachment)

Target Market(s)

Technology, Online Users Etc

Industry/Entity Type

Software Developer

Number of Pages Required

1 page

Font styles to use
Sans Serif

Colors
34a7d8
0493ce
3176b5
85acd3

Requirements
Must have
• Looks like a well built software - examples:
https://gravelmoor.io/
https://quintaro.com/

All the images should look very professional, as though you are using it on the online platform itself.
Nice to have
• Refer to attached "Feature Listing" and Logo

```html
<!DOCTYPE html>
<html lang="en">
<head>
<meta charset="utf-8">
<title>Eventra – Platform Interface</title>
<link href="https://fonts.googleapis.com/css2?family=Montserrat:wght@400;500;600;700;800&display=swap" rel="stylesheet">
<style>
:root{
  --stage-grey:#a3a3a3;
  --accent-sky:#45c4fb;
  --brand-navy:#141b3d;
  --nav-blue:#3176b5;
  --nav-active:#3fb6f0;
  --footer-blue:#1f5b97;
  --soft-blue:#85acd3;
  --mid-blue:#3176b5;
  --bright-blue:#34a7d8;
  --button-blue:#3fb9f2;
  --panel-bg:#e3eef6;
  --card-line:#d3dbe3;
  --ink:#1c1c1c;
  --muted:#6b6b6b;
  --white:#ffffff;
}
*{box-sizing:border-box;margin:0;padding:0}
html,body{width:1200px;height:936px;overflow:hidden}
body{font-family:"Montserrat",sans-serif;background:var(--stage-grey);position:relative;color:var(--ink)}
.backdrop{position:absolute;inset:0}
.screen{position:absolute;width:553px;height:413px;background:var(--panel-bg);box-shadow:0 4px 10px rgba(0,0,0,.35);overflow:hidden}
.screen--events{left:39px;top:46px}
.screen--breakouts{left:608px;top:46px}
.screen--rewards{left:39px;top:478px}

.topbar{position:absolute;left:0;top:0;width:553px;height:49px;background:var(--white);box-shadow:0 1px 3px rgba(0,0,0,.08)}
.brand{position:absolute;left:20px;top:14px;font-weight:800;font-size:19px;letter-spacing:-.5px;color:var(--brand-navy)}
.duration{position:absolute;left:312px;top:25px;font-size:6.5px;font-weight:700;letter-spacing:.2px}
.timer{position:absolute;left:387px;top:16px;width:146px}
.timer__labels{display:flex;justify-content:space-between;font-size:5px;color:#333}
.timer__track{margin-top:4px;height:3px;background:#e6e6e6;border-radius:2px}
.timer__fill{width:50px;height:3px;background:var(--mid-blue);border-radius:2px}

.sidenav{position:absolute;left:0;top:49px;width:66px;height:333px;background:var(--nav-blue);display:flex;flex-direction:column}
.sidenav__item{flex:1;display:flex;flex-direction:column;align-items:center;justify-content:center;color:var(--white);font-size:6.5px;font-weight:700;text-align:center;line-height:1.45;border-bottom:1px solid rgba(255,255,255,.12)}
.sidenav__item svg{width:10px;height:10px;margin-bottom:4px;fill:var(--white)}
.sidenav__item--tall{flex:1.15}
.sidenav__item--active{background:var(--nav-active)}

.footer{position:absolute;left:0;bottom:0;width:553px;height:31px;background:var(--footer-blue);color:#dbe6f2;font-size:6.5px;display:flex;align-items:center;justify-content:center}

.workspace{position:absolute;left:72px;top:56px;width:475px;height:298px;background:var(--white);box-shadow:0 1px 4px rgba(0,0,0,.08)}

.column{position:absolute;top:7px;width:142px;height:284px;border:1px solid var(--card-line);background:var(--white)}
.column--agenda{left:8px}
.column--programs{left:166px}
.column--speakers{left:324px;width:141px}
.column__head{margin:2px;height:23px;color:var(--white);font-weight:700;font-size:8.5px;display:flex;align-items:center;justify-content:center;letter-spacing:.2px}
.head--soft{background:var(--soft-blue)}
.head--deep{background:var(--mid-blue)}

.photo{position:absolute;display:block}
.agenda__photo{left:7px;top:33px;width:127px;height:121px;background:linear-gradient(135deg,#c9d3dc,#7d8a96 55%,#3b4652)}
.agenda__text{position:absolute;left:6px;top:169px;width:130px;font-size:5.6px;line-height:9.2px;color:var(--muted);text-align:center}
.pill{position:absolute;height:21px;width:66px;border-radius:11px;background:var(--button-blue);color:var(--white);font-size:5.8px;font-weight:500;display:flex;align-items:center;justify-content:center;left:38px;top:238px}

.program{position:absolute;left:7px;width:128px;height:55px;border-bottom:1px solid #e4e8ec}
.program:nth-of-type(1){top:33px}
.program:nth-of-type(2){top:99px}
.program:nth-of-type(3){top:165px;border-bottom:none}
.program__thumb{position:absolute;left:0;top:0;width:53px;height:49px;background:linear-gradient(160deg,#0e2238,#173a5c 60%,#0b1a2b)}
.program__title{position:absolute;left:62px;top:4px;font-size:7px;font-weight:600}
.program__blurb{position:absolute;left:62px;top:17px;width:70px;font-size:5.6px;line-height:9.2px;color:var(--muted)}

.speaker{position:absolute;width:62px;text-align:center}
.speaker__photo{width:62px;height:58px;background:linear-gradient(180deg,#d8c2ae,#8e7563)}
.speaker__name{margin-top:8px;font-size:5.8px;font-weight:600}
.scrollthumb{position:absolute;right:0;top:92px;width:2px;height:26px;background:#c8ccd1}

.room{position:absolute;top:7px;width:226px;height:100px;border:1px solid var(--card-line);background:var(--white);text-align:center}
.room--one{left:8px}
.room--two{left:241px}
.room__head{margin:2px;height:25px;background:var(--soft-blue);color:var(--white);font-weight:700;font-size:8.8px;display:flex;align-items:center;justify-content:center;letter-spacing:.3px}
.room__count{margin-top:11px;font-size:12px;font-weight:700;color:var(--mid-blue)}
.room__time{margin-top:2px;font-size:8px;font-weight:500}
.room__link{margin-top:5px;font-size:8px;font-weight:500}

.achievements{position:absolute;left:35px;top:30px;list-style:none}
.achievements li{display:flex;align-items:center;height:27px;font-size:16px;font-weight:500;color:var(--mid-blue)}
.achievements svg{width:14px;height:14px;margin-right:7px}
.score{position:absolute;left:288px;top:27px;width:86px;height:86px}
.score__value{position:absolute;left:0;top:24px;width:86px;text-align:center;font-size:19px;font-weight:700}
.score__label{position:absolute;left:0;top:51px;width:86px;text-align:center;font-size:8px}
.collect{position:absolute;left:34px;top:138px;font-size:13px;font-weight:700}
.collect-note{position:absolute;left:34px;top:173px;font-size:9.6px;line-height:19px;color:#333}
.collect-note a{color:var(--mid-blue)}
</style>
</head>
<body>
<svg class="backdrop" width="1200" height="936" viewBox="0 0 1200 936" aria-hidden="true">
  <path d="M527 936 Q600 520 1110 410 L1200 446 L1200 936 Z" fill="var(--accent-sky)"/>
</svg>

<!-- Event info screen -->
<section class="screen screen--events">
  <header class="topbar">
    <div class="brand">EVENTRA</div>
    <div class="duration">EVENT DURATION</div>
    <div class="timer"><div class="timer__labels"><span>Time Left</span><span>(HH:MM)</span></div><div class="timer__track"><div class="timer__fill"></div></div></div>
  </header>
  <nav class="sidenav">
    <div class="sidenav__item sidenav__item--active"><svg viewBox="0 0 10 10"><circle cx="5" cy="5" r="5"/><rect x="4.3" y="4" width="1.4" height="4" fill="var(--nav-active)"/><circle cx="5" cy="2.7" r=".8" fill="var(--nav-active)"/></svg>EVENT INFO</div>
    <div class="sidenav__item"><svg viewBox="0 0 10 10"><path d="M0 1h3v2H0zM3.5 1h3v2h-3zM7 1h3v2H7zM0 4h3v2H0zM3.5 4h3v2h-3zM7 4h3v2H7zM0 7h3v2H0zM3.5 7h3v2h-3zM7 7h3v2H7z"/></svg>STAGE</div>
    <div class="sidenav__item"><svg viewBox="0 0 10 10"><path d="M0 0h1v9h9v1H0z"/><path d="M1.5 7.5 4 4.5l2 1.5 3-4" fill="none" stroke="#fff" stroke-width="1"/></svg>BREAKOUTS</div>
    <div class="sidenav__item"><svg viewBox="0 0 10 10"><path d="M5 0 0 4.5h1.5V10h2.5V7h2v3h2.5V4.5H10z"/></svg>BOOTHS</div>
    <div class="sidenav__item sidenav__item--tall"><svg viewBox="0 0 10 10"><path d="M0 .5h10v7H0zM1 1.5v5h8v-5z M3.5 8.5h3V10h-3z"/></svg>VIRTUAL<br>EXHIBITION</div>
    <div class="sidenav__item sidenav__item--tall"><svg viewBox="0 0 10 10"><circle cx="5" cy="5" r="3.6"/><path d="M5 0l1 2H4zM5 10l1-2H4zM0 5l2 1V4zM10 5 8 6V4zM1.5 1.5l2.2.8-1.4 1.4zM8.5 8.5l-2.2-.8 1.4-1.4zM8.5 1.5l-.8 2.2-1.4-1.4zM1.5 8.5l.8-2.2 1.4 1.4z"/></svg>REWARDS</div>
  </nav>
  <main class="workspace">
    <article class="column column--agenda">
      <div class="column__head head--soft">AGENDA</div>
      <div class="photo agenda__photo" role="img" aria-label="Photo of a team reviewing documents at a laptop"></div>
      <p class="agenda__text">Lorem ipsum dolor sit amet, consectetur adipiscing elit, sed do eiusmod tempor incididunt ut labore et dolore magna aliqua. Ut enim ad minim veniam,quis nostrud exercitation ullamco laboris nisi ut aliquip ex ea commodo consequat.</p>
      <div class="pill">READ MORE</div>
    </article>
    <article class="column column--programs">
      <div class="column__head head--deep">PROGRAMMING</div>
      <div style="position:relative">
        <div class="program" style="top:8px"><div class="program__thumb" role="img" aria-label="Screenshot of source code"></div><div class="program__title">PROGRAM NAME</div><div class="program__blurb">Lorem ipsum dolor sit amet, consectetur adipiscing elit,</div></div>
        <div class="program" style="top:74px"><div class="program__thumb" role="img" aria-label="Screenshot of source code"></div><div class="program__title">PROGRAM NAME</div><div class="program__blurb">Lorem ipsum dolor sit amet, consectetur adipiscing elit,</div></div>
        <div class="program" style="top:140px"><div class="program__thumb" role="img" aria-label="Abstract digital code texture"></div><div class="program__title">PROGRAM NAME</div><div class="program__blurb">Lorem ipsum dolor sit amet, consectetur adipiscing elit,</div></div>
      </div>
      <div class="pill">VIEW MORE</div>
    </article>
    <article class="column column--speakers">
      <div class="column__head head--soft">SPEAKERS</div>
      <div class="speaker" style="left:6px;top:33px"><div class="speaker__photo" role="img" aria-label="Speaker portrait"></div><div class="speaker__name">JOHN DOE</div></div>
      <div class="speaker" style="left:74px;top:33px"><div class="speaker__photo" style="background:linear-gradient(180deg,#9aa3ab,#d6a93b)" role="img" aria-label="Speaker portrait"></div><div class="speaker__name">SMITHA</div></div>
      <div class="speaker" style="left:6px;top:116px"><div class="speaker__photo" style="background:linear-gradient(180deg,#a7aeb4,#5f86b0)" role="img" aria-label="Speaker portrait"></div><div class="speaker__name">OCCAECAT</div></div>
      <div class="speaker" style="left:74px;top:116px"><div class="speaker__photo" style="background:linear-gradient(180deg,#eaeaea,#c9b6a5)" role="img" aria-label="Speaker portrait"></div><div class="speaker__name">NEQUE</div></div>
      <div class="speaker" style="left:6px;top:199px"><div class="speaker__photo" style="background:linear-gradient(180deg,#c7c3bd,#c98f33)" role="img" aria-label="Speaker portrait"></div><div class="speaker__name">NOSTRUM</div></div>
      <div class="speaker" style="left:74px;top:199px"><div class="speaker__photo" style="background:linear-gradient(180deg,#cfd4d8,#6aa6d6)" role="img" aria-label="Speaker portrait"></div><div class="speaker__name">TOTAMEM</div></div>
      <div class="scrollthumb"></div>
    </article>
  </main>
  <footer class="footer">© Copyright 2020 Eventra. All Rights Reserved.</footer>
</section>

<!-- Breakouts screen -->
<section class="screen screen--breakouts">
  <header class="topbar">
    <div class="brand">EVENTRA</div>
    <div class="duration">EVENT DURATION</div>
    <div class="timer"><div class="timer__labels"><span>Time Left</span><span>(HH:MM)</span></div><div class="timer__track"><div class="timer__fill"></div></div></div>
  </header>
  <nav class="sidenav">
    <div class="sidenav__item"><svg viewBox="0 0 10 10"><circle cx="5" cy="5" r="5"/><rect x="4.3" y="4" width="1.4" height="4" fill="var(--nav-blue)"/><circle cx="5" cy="2.7" r=".8" fill="var(--nav-blue)"/></svg>EVENT INFO</div>
    <div class="sidenav__item"><svg viewBox="0 0 10 10"><path d="M0 1h3v2H0zM3.5 1h3v2h-3zM7 1h3v2H7zM0 4h3v2H0zM3.5 4h3v2h-3zM7 4h3v2H7zM0 7h3v2H0zM3.5 7h3v2h-3zM7 7h3v2H7z"/></svg>STAGE</div>
    <div class="sidenav__item sidenav__item--active"><svg viewBox="0 0 10 10"><path d="M0 0h1v9h9v1H0z"/><path d="M1.5 7.5 4 4.5l2 1.5 3-4" fill="none" stroke="#fff" stroke-width="1"/></svg>BREAKOUTS</div>
    <div class="sidenav__item"><svg viewBox="0 0 10 10"><path d="M5 0 0 4.5h1.5V10h2.5V7h2v3h2.5V4.5H10z"/></svg>BOOTHS</div>
    <div class="sidenav__item sidenav__item--tall"><svg viewBox="0 0 10 10"><path d="M0 .5h10v7H0zM1 1.5v5h8v-5z M3.5 8.5h3V10h-3z"/></svg>VIRTUAL<br>EXHIBITION</div>
    <div class="sidenav__item sidenav__item--tall"><svg viewBox="0 0 10 10"><circle cx="5" cy="5" r="3.6"/><path d="M5 0l1 2H4zM5 10l1-2H4zM0 5l2 1V4zM10 5 8 6V4zM1.5 1.5l2.2.8-1.4 1.4zM8.5 8.5l-2.2-.8 1.4-1.4zM8.5 1.5l-.8 2.2-1.4-1.4zM1.5 8.5l.8-2.2 1.4 1.4z"/></svg>REWARDS</div>
  </nav>
  <main class="workspace">
    <article class="room room--one">
      <div class="room__head">JOIN BREAKOUT ROOM 1</div>
      <div class="room__count">(4/50)</div>
      <div class="room__time">3.00pm to 4.30pm</div>
      <div class="room__link">(Link to 3rd Party Meetly Room</div>
    </article>
    <article class="room room--two">
      <div class="room__head">JOIN BREAKOUT ROOM 2</div>
      <div class="room__count">(10/50)</div>
      <div class="room__time">3.00pm to 4.30pm</div>
      <div class="room__link">(Link to 3rd Party Meetly Room)</div>
    </article>
  </main>
  <footer class="footer">© Copyright 2020 Eventra. All Rights Reserved.</footer>
</section>

<!-- Rewards screen -->
<section class="screen screen--rewards">
  <header class="topbar">
    <div class="brand">EVENTRA</div>
    <div class="duration">EVENT DURATION</div>
    <div class="timer"><div class="timer__labels"><span>Time Left</span><span>(HH:MM)</span></div><div class="timer__track"><div class="timer__fill"></div></div></div>
  </header>
  <nav class="sidenav">
    <div class="sidenav__item"><svg viewBox="0 0 10 10"><circle cx="5" cy="5" r="5"/><rect x="4.3" y="4" width="1.4" height="4" fill="var(--nav-blue)"/><circle cx="5" cy="2.7" r=".8" fill="var(--nav-blue)"/></svg>EVENT INFO</div>
    <div class="sidenav__item"><svg viewBox="0 0 10 10"><path d="M0 1h3v2H0zM3.5 1h3v2h-3zM7 1h3v2H7zM0 4h3v2H0zM3.5 4h3v2h-3zM7 4h3v2H7zM0 7h3v2H0zM3.5 7h3v2h-3zM7 7h3v2H7z"/></svg>STAGE</div>
    <div class="sidenav__item"><svg viewBox="0 0 10 10"><path d="M0 0h1v9h9v1H0z"/><path d="M1.5 7.5 4 4.5l2 1.5 3-4" fill="none" stroke="#fff" stroke-width="1"/></svg>BREAKOUTS</div>
    <div class="sidenav__item"><svg viewBox="0 0 10 10"><path d="M5 0 0 4.5h1.5V10h2.5V7h2v3h2.5V4.5H10z"/></svg>BOOTHS</div>
    <div class="sidenav__item sidenav__item--tall"><svg viewBox="0 0 10 10"><path d="M0 .5h10v7H0zM1 1.5v5h8v-5z M3.5 8.5h3V10h-3z"/></svg>VIRTUAL<br>EXHIBITION</div>
    <div class="sidenav__item sidenav__item--tall sidenav__item--active"><svg viewBox="0 0 10 10"><circle cx="5" cy="5" r="3.6"/><path d="M5 0l1 2H4zM5 10l1-2H4zM0 5l2 1V4zM10 5 8 6V4zM1.5 1.5l2.2.8-1.4 1.4zM8.5 8.5l-2.2-.8 1.4-1.4zM8.5 1.5l-.8 2.2-1.4-1.4zM1.5 8.5l.8-2.2 1.4 1.4z"/></svg>REWARDS</div>
  </nav>
  <main class="workspace">
    <ul class="achievements">
      <li><svg viewBox="0 0 14 14"><path d="M1 1h3l4 6-4 6H1l4-6z" fill="var(--bright-blue)"/><path d="M6 1h3l4 6-4 6H6l4-6z" fill="var(--mid-blue)"/></svg>Visited Virtual Exhibition</li>
      <li><svg viewBox="0 0 14 14"><path d="M1 1h3l4 6-4 6H1l4-6z" fill="var(--bright-blue)"/><path d="M6 1h3l4 6-4 6H6l4-6z" fill="var(--mid-blue)"/></svg>Joined Breakout Room</li>
      <li><svg viewBox="0 0 14 14"><path d="M1 1h3l4 6-4 6H1l4-6z" fill="var(--bright-blue)"/><path d="M6 1h3l4 6-4 6H6l4-6z" fill="var(--mid-blue)"/></svg>Checked out Booths</li>
    </ul>
    <div class="score">
      <svg width="86" height="86" viewBox="0 0 86 86" aria-hidden="true">
        <defs><linearGradient id="ring" x1="0" y1="0" x2="1" y2="1"><stop offset="0" stop-color="#45c4fb"/><stop offset=".5" stop-color="#2450e6"/></linearGradient></defs>
        <circle cx="43" cy="43" r="41" fill="none" stroke="url(#ring)" stroke-width="2.2"/>
      </svg>
      <div class="score__value">40/100</div>
      <div class="score__label">Total Points</div>
    </div>
    <h2 class="collect">Collect Reward - Trigger Email/Link to 3rd Party App</h2>
    <p class="collect-note">(Flash them a PROMO CODE/“Email will be given to you on how you can claim your prize)<br>- they can go to <a href="#">www.prizeharbor.com</a> to claim</p>
  </main>
  <footer class="footer">© Copyright 2020 Eventra. All Rights Reserved.</footer>
</section>
</body>
</html>
```